MRT Property - Business Cards

Looking for a business card & general letterhead, signage etc design for our new logo.

Colours:
000a20
0056a2
00b5ef
0088ce
68cef2

Fonts:
Poppins
Karla

Please keep look and feel of new brand - example in the zip package I sent.

```html
<!DOCTYPE html>
<html lang="en">
<head>
<meta charset="utf-8">
<title>MRT Property – Business Cards</title>
<link href="https://fonts.googleapis.com/css2?family=Poppins:ital,wght@0,300;0,400;0,600;0,800;1,300&display=swap" rel="stylesheet">
<style>
  :root {
    --ink: #000a20;
    --stage: #14161b;
    --brand-blue: #0056a2;
    --cyan: #00b5ef;
    --mid-blue: #0088ce;
    --sky: #68cef2;
    --white: #ffffff;
  }
  * { margin: 0; padding: 0; box-sizing: border-box; }
  html, body { width: 1200px; height: 900px; overflow: hidden; }
  body {
    background: var(--stage);
    font-family: "Poppins", sans-serif;
    display: flex;
    align-items: center;
    justify-content: center;
    gap: 48px;
  }
  .card {
    position: relative;
    width: 540px;
    height: 309px;
    border-radius: 22px;
    background: var(--brand-blue);
    color: var(--white);
    overflow: hidden;
    box-shadow: 0 18px 40px rgba(0, 0, 0, 0.55);
  }

  /* Front */
  .card-front .wordmark {
    position: absolute;
    left: 48px;
    top: 92px;
    width: 210px;
    font-weight: 800;
    font-size: 40px;
    line-height: 1.05;
    color: var(--white);
    display: flex;
    align-items: center;
    gap: 12px;
  }
  .wordmark .mark-dot {
    flex: none;
    width: 18px;
    height: 18px;
    border-radius: 50%;
    background: var(--sky);
  }
  .card-front .divider {
    position: absolute;
    left: 282px;
    top: 72px;
    width: 1px;
    height: 132px;
    background: var(--mid-blue);
  }
  .card-front .contact {
    position: absolute;
    left: 302px;
    top: 78px;
  }
  .contact .person-name {
    font-weight: 800;
    font-size: 26px;
    letter-spacing: 0.5px;
    text-transform: uppercase;
    color: var(--cyan);
    line-height: 1.1;
  }
  .contact .person-role {
    font-weight: 300;
    font-size: 14px;
    margin-bottom: 10px;
  }
  .contact ul { list-style: none; }
  .contact li {
    display: flex;
    align-items: center;
    gap: 7px;
    font-weight: 300;
    font-size: 13.5px;
    line-height: 1.55;
  }
  .contact svg { width: 11px; height: 11px; flex: none; }
  .card-front .address {
    position: absolute;
    left: 48px;
    bottom: 44px;
    font-weight: 300;
    font-size: 13.5px;
  }

  /* Back */
  .card-back .pattern {
    position: absolute;
    inset: 0;
    background:
      repeating-linear-gradient(150deg, rgba(0, 136, 206, 0.35) 0 18px, rgba(0, 10, 32, 0.18) 18px 36px),
      linear-gradient(135deg, #0a62b8, var(--brand-blue) 55%, #0a4c92);
  }
  .card-back .wordmark {
    position: absolute;
    right: 40px;
    bottom: 40px;
    font-weight: 800;
    font-size: 30px;
    line-height: 1.05;
    color: var(--white);
    display: flex;
    align-items: center;
    gap: 10px;
  }
  .card-back .wordmark .mark-dot { width: 14px; height: 14px; }
</style>
</head>
<body>

  <section class="card card-front">
    <div class="wordmark"><span class="mark-dot"></span><span>MRT Property</span></div>
    <div class="divider"></div>
    <div class="contact">
      <p class="person-name">Dana Whitlock</p>
      <p class="person-role">Founder &amp; Principal</p>
      <ul>
        <li>
          <svg viewBox="0 0 12 12" fill="none" stroke="#68cef2" stroke-width="1.4"><path d="M2.5 1.5l2 .2.8 2.3-1.2 1a6 6 0 0 0 3 3l1-1.2 2.3.8.2 2c-4.5.6-9-3.9-8.1-8.1z"/></svg>
          +1- 555-014-2290
        </li>
        <li>
          <svg viewBox="0 0 12 12" fill="none" stroke="#68cef2" stroke-width="1.2"><rect x="1" y="2.5" width="10" height="7" rx="1"/><path d="M1 3l5 3.5L11 3"/></svg>
          info@mrtproperty.com
        </li>
        <li>
          <svg viewBox="0 0 12 12" fill="none" stroke="#68cef2" stroke-width="1.1"><circle cx="6" cy="6" r="5"/><ellipse cx="6" cy="6" rx="2.2" ry="5"/><path d="M1 6h10"/></svg>
          www.mrtproperty.com
        </li>
      </ul>
    </div>
    <p class="address">4120 Harlow Avenue #18, Suite Brookfield Park</p>
  </section>

  <section class="card card-back">
    <div class="pattern" role="img" aria-label="Repeating brand pattern of layered blue swoosh shapes"></div>
    <div class="wordmark"><span class="mark-dot"></span><span>MRT Property</span></div>
  </section>

</body>
</html>
```